Dultavo.com webside

I want to build a Dultavo.com retail website use on Shopify, reselling three main categories: Office Supplies, Packing Supplies, and Home Consumables. I also wish the webpage has the same functions as the Zelvik home page. The page is split into three different parts with the top being a sliding screen showcasing promotion products, below it being the three categories, and finally, a moving screen showing company missions.
Target Market(s)
U.S online
Industry/Entity Type
Office Supplies, packing Supplies and Home Consumables
Coding
Coded - Design and coding required
Number of Pages Required
5+ page
Look and feel

```html
<!DOCTYPE html>
<html lang="en">
<head>
<meta charset="utf-8">
<title>Dultavo – Office, Packing &amp; Home Supplies</title>
<link rel="stylesheet" href="https://fonts.googleapis.com/css2?family=Poppins:wght@400;500;600;700;800&family=Lato:wght@400;700&display=swap">
<style>
:root{
  --teal:#14a98b;
  --teal-soft:#6fd3bd;
  --mint:#c6efe6;
  --mint-pale:#eaf8f4;
  --ink:#111111;
  --text:#222222;
  --muted:#7a7a7a;
  --line:#dcdcdc;
  --footer:#121212;
  --white:#ffffff;
}
*{margin:0;padding:0;box-sizing:border-box}
html,body{width:1200px;height:3607px;overflow:hidden;background:var(--white)}
body{position:relative;font-family:'Poppins',sans-serif;color:var(--text)}
.abs{position:absolute}
.photo{position:absolute}

/* header */
.site-header{position:absolute;left:0;top:0;width:1200px;height:92px;background:var(--white)}
.menu-toggle{left:111px;top:38px;width:25px;height:20px}
.menu-toggle span{display:block;height:3px;background:var(--ink);margin-bottom:5px;border-radius:1px}
.brand{left:0;width:1200px;top:20px;text-align:center;font-size:46px;font-weight:600;color:var(--ink);letter-spacing:.5px}
.header-icons{right:112px;top:38px;display:flex;gap:22px}
.header-icons svg{width:20px;height:20px;fill:var(--teal)}

/* hero */
.hero{position:absolute;left:0;top:92px;width:1200px;height:600px;background:var(--mint)}
.hero-photo{left:0;top:0;width:600px;height:600px;background:linear-gradient(135deg,#5f6770 0%,#4a5058 35%,#c94a8e 55%,#f1b23b 70%,#3aa5d8 85%,#e5e6ea 100%)}
.hero-kicker{left:689px;top:102px;font-size:21px;font-weight:400;color:var(--ink)}
.hero-title{left:689px;top:150px;font-size:43px;font-weight:800;line-height:64px;color:var(--ink);letter-spacing:-.3px}
.btn-outline{position:absolute;display:flex;align-items:center;justify-content:center;border:2px solid var(--teal);color:var(--ink);font-size:15px;font-weight:500;background:transparent}
.hero .btn-outline{left:690px;top:307px;width:116px;height:49px}
.hero-thumb{top:401px;width:161px;height:134px}
.hero-thumb.active{outline:4px solid var(--teal);outline-offset:-4px}

/* categories */
.cat-title{left:111px;top:808px;font-size:31px;font-weight:700;line-height:47px;color:var(--ink)}
.cat-intro{left:111px;top:918px;font-size:15px;line-height:26px;color:var(--text)}
.categories .btn-outline{left:111px;top:997px;width:116px;height:49px;font-size:15px}
.cat-card{position:absolute;top:777px;width:222px;height:324px}
.cat-card .photo{left:0;top:0;width:222px;height:324px}
.cat-label{position:absolute;left:13px;top:241px;width:197px;height:71px;background:var(--white);padding:18px 0 0 13px}
.cat-label h3{font-size:13px;font-weight:600;color:var(--ink)}
.cat-label p{font-size:11px;color:var(--muted);margin-top:3px;font-family:'Lato',sans-serif}
.cat-label .go{position:absolute;right:13px;top:24px;width:26px;height:26px;border-radius:50%;background:var(--teal-soft)}

/* top selling */
.section-title{left:0;width:1200px;text-align:center;font-size:31px;font-weight:600;color:var(--ink)}
.tabs{left:0;width:1200px;top:1253px;display:flex;justify-content:center;gap:50px;font-size:17px;font-weight:500;color:var(--ink)}
.tab-rule{left:111px;top:1299px;width:977px;height:1px;background:var(--line)}
.tab-active{left:349px;top:1297px;width:126px;height:3px;background:var(--teal)}
.product{position:absolute;top:1351px;width:225px}
.product .tile{width:225px;height:223px;background:var(--mint-pale);position:relative}
.product .tile .photo{left:50px;top:35px;width:125px;height:150px;border-radius:6px}
.product h4{margin-top:22px;font-size:17px;font-weight:400;color:var(--ink)}
.product .price{margin-top:6px;font-size:22px;font-weight:600;color:var(--teal)}
.slider-arrow{position:absolute;top:1449px;width:27px;height:27px;border-radius:50%;background:var(--teal-soft)}
.slider-arrow svg,.cat-label .go svg{width:100%;height:100%}

/* missions */
.missions{position:absolute;left:0;top:1739px;width:1200px;height:557px;background:radial-gradient(ellipse at 75% 85%,#8a6a70 0%,#4a4440 35%,#2c2a28 70%),#2c2a28}
.missions h2{position:absolute;left:0;width:1200px;top:170px;text-align:center;font-size:31px;font-weight:700;color:var(--teal)}
.missions p{position:absolute;left:215px;width:770px;top:246px;text-align:center;font-family:'Lato',sans-serif;font-size:15.5px;line-height:25.7px;color:var(--white)}

/* blogs */
.post{position:absolute;top:2457px;width:316px}
.post .photo{position:relative;width:316px;height:196px}
.post .date{position:absolute;left:28px;top:175px;width:141px;height:42px;background:var(--teal);color:var(--white);font-size:13px;display:flex;align-items:center;justify-content:center}
.post h3{margin-top:50px;font-size:20.5px;font-weight:400;line-height:28px;color:var(--ink)}
.post p{margin-top:8px;font-family:'Lato',sans-serif;font-size:15px;line-height:25px;color:var(--muted)}
.post a{display:block;margin-top:14px;font-size:15px;font-weight:600;color:var(--teal);text-decoration:none}

/* perks */
.perks{position:absolute;left:0;top:2932px;width:1200px;height:297px;background:var(--mint-pale)}
.perk{position:absolute;top:98px;width:240px;margin-left:-120px;text-align:center}
.perk svg{width:66px;height:66px;stroke:var(--teal);fill:none;stroke-width:2.4;stroke-linecap:round;stroke-linejoin:round}
.perk span{display:block;margin-top:22px;font-size:15px;font-weight:500;color:var(--ink)}

/* footer */
.site-footer{position:absolute;left:0;top:3229px;width:1200px;height:378px;background:var(--footer);color:var(--white);font-family:'Lato',sans-serif}
.foot-col{position:absolute;top:92px}
.foot-col h4{font-family:'Poppins',sans-serif;font-size:21px;font-weight:500;letter-spacing:.3px}
.foot-col ul{list-style:none;margin-top:24px}
.foot-col li{font-size:15px;line-height:25.7px}
.contact li{display:flex;align-items:center;gap:12px;line-height:38px}
.contact svg{width:16px;height:16px;fill:var(--white)}
.newsletter{position:absolute;left:805px;top:152px;width:283px;height:49px;border:1px solid #cfcfcf;border-radius:25px}
.newsletter span{position:absolute;left:21px;top:14px;font-size:15px;color:#cfcfcf}
.newsletter b{position:absolute;right:4px;top:4px;width:87px;height:39px;border-radius:20px;background:var(--white);color:#333;font-weight:400;font-size:15px;display:flex;align-items:center;justify-content:center}
.social{position:absolute;left:906px;top:228px;display:flex;gap:20px}
.social i{width:17px;height:17px;border-radius:50%;background:var(--white);display:block}
.copyright{position:absolute;left:113px;top:318px;font-size:15px}
.payments{position:absolute;left:805px;top:318px;display:flex;gap:6px}
.payments i{display:block;width:41px;height:25px;border-radius:3px}
</style>
</head>
<body>

<header class="site-header">
  <div class="abs menu-toggle" aria-label="Menu"><span></span><span></span><span></span></div>
  <div class="abs brand">Dultavo</div>
  <div class="abs header-icons">
    <svg viewBox="0 0 24 24" aria-label="Search"><path d="M10 3a7 7 0 0 1 5.6 11.2l5.1 5.1-1.8 1.8-5.1-5.1A7 7 0 1 1 10 3zm0 2.6a4.4 4.4 0 1 0 0 8.8 4.4 4.4 0 0 0 0-8.8z"/></svg>
    <svg viewBox="0 0 24 24" aria-label="Account"><circle cx="12" cy="7" r="5"/><path d="M3 23c0-6 4-9 9-9s9 3 9 9z"/></svg>
    <svg viewBox="0 0 24 24" aria-label="Cart"><path d="M1 3h4l1 3h17l-3 9H8.5l.6 2H20v2H7.6L3.6 5H1z"/><circle cx="9" cy="21.5" r="1.8"/><circle cx="18" cy="21.5" r="1.8"/></svg>
  </div>
</header>

<section class="hero">
  <div class="photo hero-photo" role="img" aria-label="Colourful office stationery: pens, pencils, clips and pins on a grey desk"></div>
  <div class="abs hero-kicker">SPECIAL OFFER DISCOUNT 10% OFF</div>
  <h1 class="abs hero-title">BIGGEST OFFER ON<br>ALL COLLECTIONS</h1>
  <a class="btn-outline">SHOP NOW</a>
  <div class="photo hero-thumb active" style="left:566px;background:linear-gradient(135deg,#5d646c,#c9508f 60%,#f0b03c)" role="img" aria-label="Stationery slide preview"></div>
  <div class="photo hero-thumb" style="left:746px;background:linear-gradient(180deg,#d9d4cc,#b58a5c 55%,#8d6440)" role="img" aria-label="Warehouse cardboard boxes slide preview"></div>
  <div class="photo hero-thumb" style="left:927px;background:linear-gradient(180deg,#b9bcc4,#4a5c8a 50%,#c8a040)" role="img" aria-label="Shelves of home consumables slide preview"></div>
</section>

<section class="categories">
  <h2 class="abs cat-title">Our<br>Categories</h2>
  <p class="abs cat-intro">Lorem ipsum dolor sit amet,<br>consectetur adipiscing</p>
  <a class="btn-outline">SHOP NOW</a>

  <div class="cat-card" style="left:356px">
    <div class="photo" style="background:linear-gradient(160deg,#4c5a34,#8b2a2a 45%,#c9c6c0 80%)" role="img" aria-label="Pen holder with scissors and stationery"></div>
    <div class="cat-label"><h3>Office Supplies</h3><p>Lorem ipsum</p><span class="go"><svg viewBox="0 0 26 26"><path d="M8 13h10m-3-3 3 3-3 3" stroke="#fff" stroke-width="1.4" fill="none"/></svg></span></div>
  </div>
  <div class="cat-card" style="left:611px">
    <div class="photo" style="background:linear-gradient(180deg,#b7b3ad,#a5825c 55%,#8e6a45)" role="img" aria-label="Cardboard box in a warehouse aisle"></div>
    <div class="cat-label"><h3>Packing Supplies</h3><p>Lorem ipsum</p><span class="go"><svg viewBox="0 0 26 26"><path d="M8 13h10m-3-3 3 3-3 3" stroke="#fff" stroke-width="1.4" fill="none"/></svg></span></div>
  </div>
  <div class="cat-card" style="left:867px">
    <div class="photo" style="background:linear-gradient(180deg,#e9ecef,#7dc3e0 45%,#9ccf3c 75%,#e3e4e6)" role="img" aria-label="Bucket of cleaning products and mop"></div>
    <div class="cat-label"><h3>Home Consumables</h3><p>Lorem ipsum</p><span class="go"><svg viewBox="0 0 26 26"><path d="M8 13h10m-3-3 3 3-3 3" stroke="#fff" stroke-width="1.4" fill="none"/></svg></span></div>
  </div>
</section>

<section class="top-selling">
  <h2 class="abs section-title" style="top:1180px">Top Selling Brand</h2>
  <nav class="abs tabs"><span>Office Supplies</span><span>Packing Supplies</span><span>Home Consumables</span></nav>
  <div class="abs tab-rule"></div>
  <div class="abs tab-active"></div>

  <div class="product" style="left:111px"><div class="tile"><div class="photo" style="background:linear-gradient(180deg,#e4503a,#3a8a4a 40%,#f5e02a 55%)" role="img" aria-label="Yellow cup of coloured pencils"></div></div><h4>Product Name</h4><div class="price">$58</div></div>
  <div class="product" style="left:361px"><div class="tile"><div class="photo" style="background:linear-gradient(180deg,#d8dadd,#a9adb3)" role="img" aria-label="Office printer"></div></div><h4>Product Name</h4><div class="price">$58</div></div>
  <div class="product" style="left:612px"><div class="tile"><div class="photo" style="background:linear-gradient(180deg,#eaf8f4,#9ea3a8 40%,#151515 60%)" role="img" aria-label="Black binder clip"></div></div><h4>Product Name</h4><div class="price">$58</div></div>
  <div class="product" style="left:862px"><div class="tile"><div class="photo" style="background:linear-gradient(135deg,#c44,#e8d23a 45%,#2a2a2a 75%)" role="img" aria-label="Assorted desk supplies with scissors and stapler"></div></div><h4>Product Name</h4><div class="price">$58</div></div>

  <span class="slider-arrow" style="left:96px"><svg viewBox="0 0 27 27"><path d="M19 13.5H8m3-3-3 3 3 3" stroke="#fff" stroke-width="1.4" fill="none"/></svg></span>
  <span class="slider-arrow" style="left:1074px"><svg viewBox="0 0 27 27"><path d="M8 13.5h11m-3-3 3 3-3 3" stroke="#fff" stroke-width="1.4" fill="none"/></svg></span>
</section>

<section class="missions" role="img" aria-label="Blurred room with cleaning supplies and gloves in a basket">
  <h2>Our Missions</h2>
  <p>Lorem ipsum dolor sit amet, consectetur adipiscing elit, sed do eiusmod tempor incididunt ut labore et dolore magna aliqua. Ut enim ad minim veniam, quis nostrud exercitation ullamco laboris nisi ut aliquip ex ea commodo consequat. Duis aute irure dolor in reprehenderit in voluptate velit esse cillum dolore eu fugiat nulla pariatur. Excepteur sint occaecat cupidatat non proident, sunt in culpa qui officia deserunt mollit anim id est laborum.</p>
</section>

<section class="blogs">
  <h2 class="abs section-title" style="top:2376px">Latest Blogs</h2>
  <article class="post" style="left:111px">
    <div class="photo" style="background:linear-gradient(180deg,#4fb4de,#8fcbe6 45%,#f1f1ef 75%,#e7b3c6)" role="img" aria-label="Bottles of household cleaning products"><span class="date">17 October,2022</span></div>
    <h3>Sed ut perspiciatis unde omnis iste natus error sit</h3>
    <p>Lorem ipsum dolor sit amet, consectetur adipiscing elit, sed do eiusmod tempor</p>
    <a>READ MORE</a>
  </article>
  <article class="post" style="left:441px">
    <div class="photo" style="background:linear-gradient(180deg,#d2cdc5,#b08a60 50%,#8a6542)" role="img" aria-label="Stacked cardboard boxes in a warehouse"><span class="date">17 October,2022</span></div>
    <h3>Sed ut perspiciatis unde omnis iste natus error sit</h3>
    <p>Lorem ipsum dolor sit amet, consectetur adipiscing elit, sed do eiusmod tempor</p>
    <a>READ MORE</a>
  </article>
  <article class="post" style="left:773px">
    <div class="photo" style="background:linear-gradient(160deg,#3c3f44,#8a8d92 40%,#efe8dc 70%,#b9bcc0)" role="img" aria-label="Notebook, pen, mouse and phone on a desk"><span class="date">17 October,2022</span></div>
    <h3>Sed ut perspiciatis unde omnis iste natus error sit</h3>
    <p>Lorem ipsum dolor sit amet, consectetur adipiscing elit, sed do eiusmod tempor</p>
    <a>READ MORE</a>
  </article>
</section>

<section class="perks">
  <div class="perk" style="left:184px">
    <svg viewBox="0 0 66 66"><circle cx="35" cy="35" r="16"/><path d="M14 35a21 21 0 1 0 8-16.5M22 10v9h-9"/><path d="M39 29c-1-2-3-2.5-4-2.5-2.5 0-4 1.2-4 3s1.5 2.5 4 3 4 1.5 4 3.3-2 3-4 3-3.5-.8-4.3-2.3M35 24v3m0 16v-3"/></svg>
    <span>30 Days Money Back</span>
  </div>
  <div class="perk" style="left:461px">
    <svg viewBox="0 0 66 66"><path d="M33 4a29 29 0 1 1-27 18M6 10v12h12"/><text x="33" y="40" text-anchor="middle" font-family="Poppins,sans-serif" font-size="17" font-weight="600" fill="#14a98b" stroke="none">24/7</text></svg>
    <span>Support 24/7</span>
  </div>
  <div class="perk" style="left:737px">
    <svg viewBox="0 0 66 66"><rect x="6" y="22" width="54" height="34" rx="3"/><path d="M6 30h54M6 36h54M36 44h16v6H36zM12 50h14"/><rect x="24" y="8" width="12" height="14" rx="2"/><path d="M27 8V5h6v3"/></svg>
    <span>100% Secure Checkout</span>
  </div>
  <div class="perk" style="left:1014px">
    <svg viewBox="0 0 66 66"><path d="M33 4l7 5 8-1 3 8 7 4-2 8 4 7-6 6-1 8-8 2-5 7-7-3-7 3-5-7-8-2-1-8-6-6 4-7-2-8 7-4 3-8 8 1z"/><path d="M24 42l18-18"/><circle cx="25" cy="25" r="4"/><circle cx="41" cy="41" r="4"/></svg>
    <span>Offers Worldwide</span>
  </div>
</section>

<footer class="site-footer">
  <div class="foot-col" style="left:111px"><h4>QUICK LINKS</h4><ul><li>Home</li><li>Shop</li><li>About</li><li>Contact</li><li>FAQ</li></ul></div>
  <div class="foot-col" style="left:332px"><h4>OTHER LINKS</h4><ul><li>Report</li><li>Terms &amp; Conditions</li><li>Privacy Policy</li><li>About Us</li><li>Support</li></ul></div>
  <div class="foot-col contact" style="left:557px"><h4>CONTACT</h4>
    <ul style="margin-top:14px">
      <li><svg viewBox="0 0 16 16"><path d="M8 0a5.5 5.5 0 0 1 5.5 5.5C13.5 10 8 16 8 16S2.5 10 2.5 5.5A5.5 5.5 0 0 1 8 0zm0 3.3a2.2 2.2 0 1 0 0 4.4 2.2 2.2 0 0 0 0-4.4z"/></svg>Lorem ipsum dolor sit</li>
      <li><svg viewBox="0 0 16 16"><path d="M3.5 0.5 6 3.5 4.6 5.6c1 2.2 2.6 3.8 4.8 4.8L11.5 9l3 2.5-1.3 3C7 14.2 1.8 9 1.5 2.8z"/></svg>+1 (555) 014 2290</li>
      <li><svg viewBox="0 0 16 16"><path d="M1 3h14v10H1zm1.2 1.2L8 8.6l5.8-4.4z" fill-rule="evenodd"/></svg>info@Dultavo.com</li>
    </ul>
  </div>
  <div class="foot-col" style="left:808px"><h4>NEWSLETTER SIGN UP</h4></div>
  <div class="newsletter"><span>Your Email</span><b>SUBMIT</b></div>
  <div class="social" aria-label="Social links"><i></i><i></i><i></i><i></i><i></i></div>
  <div class="copyright">©Copyrights 2022 Dultavo &nbsp;|&nbsp;&nbsp; All Rights Reserved</div>
  <div class="payments" aria-label="Accepted payment methods">
    <i style="background:#3a3a3a"></i><i style="background:#e9c23a"></i><i style="background:#ffffff"></i><i style="background:#f2f2f2"></i><i style="background:#2f7fc9"></i><i style="background:#e64a2e"></i>
  </div>
</footer>

</body>
</html>
```